Fitness Equipment & Service

I want to make the card eye catching and fun. We are called Corvane Motion Limited and we are based in Wales. We sell, install and service all types of fitness equipment from Skipping ropes, right through the Dumbbells, Kettle bells and Barbells through to state of the art Treadmills, Running Machines and Strength Equipment. We also design and install changing room furniture and lockers.

TYPOGRAPHY
We would like to use Futrura. Futura has an appearance of efficiency and forwardness. The typeface is derived
from simple geometric forms (near-perfect circles, triangles and squares) and is based on strokes of
near-even weight, which are low in contrast. This is most visible in the almost perfectly round stroke of
the o, which is nonetheless slightly ovoid.
The lowercase has tall ascenders, which rise above the cap line. The uppercase
characters present proportions similar to those of classical Roman capitals.

TYPOGRAPHIC CONSIDERATIONS
No Strike though
No Horizontal Scaling
No Drop Shadows
No Effects
Never use less than 120% Leading

OUR CORPORATE COLOURS
BRAND GUIDELINES
We were thinking that our primary colour palette consists of the Acid Green (Pantone 382) and Process Black.

We work closely with tquarly Ltd and would like to include their name on the card somewhere. I have attached images of the other brands that we work with as an idea or the small icons I have included that illustrate what we do?. I have very kindly been given permission to use any of the images off the files that I have included below, so I hope these help. I will include these below. I would be open to suggestions if it made the card more striking Can you do it?
Updates

Hi All, Just wanted to add a few thoughts but you are the guys with the creative visions (thats why are here) We are based in Wales, UK and we would be open to lots of different ideas on a theme but must be eye catching, Bold and FUN. If you can or think that the Welsh or any dragon could be put in there then go for it (its not a must have) We have also added some ideas for colour but again its over to you!! GO FOR IT ! Thanks and look forward to your visions! Owen

Hi All, Just thought I would sen through the contact details that need to be on the card. (if you want to play around with icons instead of the wording twitter, Facebook, go for it): Corvane Motion Limited Owen Pritchard Managing Director Mob: +44 (0)7582 913 406 e-mail: sales@corvanemotion.co.uk Web: Corvanemotion.co.uk twitter: @motionLetterbin Facebook: Corvane Motion Limited

```html
<!DOCTYPE html>
<html lang="en">
<head>
<meta charset="utf-8">
<title>Corvane Motion Limited – Business Card</title>
<link rel="stylesheet" href="https://fonts.googleapis.com/css2?family=Jost:wght@500;600&family=Arimo:wght@400&display=swap">
<style>
  :root {
    --stage: #e9ebef;
    --navy: #12174a;
    --navy-deep: #0c1038;
    --blue: #1a5fae;
    --blue-mid: #1f6fc0;
    --blue-dark: #0f3f78;
    --cyan: #33a6dd;
    --slate: #7c93a8;
    --tile-dark: #143a66;
    --white: #ffffff;
    --paper: #f3f4f6;
  }
  * { margin: 0; padding: 0; box-sizing: border-box; }
  html, body { width: 1200px; height: 902px; overflow: hidden; }
  body { background: var(--stage); position: relative; font-family: "Arimo", Arial, sans-serif; }

  .card {
    position: absolute;
    left: 250px;
    width: 700px;
    height: 400px;
    overflow: hidden;
    box-shadow: 0 4px 14px rgba(0,0,0,.18);
  }
  .card--back { top: 30px; background: linear-gradient(135deg, var(--blue-dark) 0%, var(--blue) 55%, var(--blue-mid) 100%); }
  .card--front { top: 472px; }

  /* back face */
  .backdrop-photo {
    position: absolute; inset: 0;
    background: radial-gradient(ellipse at 75% 10%, rgba(10,30,70,.55) 0%, rgba(10,30,70,0) 55%),
                radial-gradient(ellipse at 30% 85%, rgba(10,30,70,.45) 0%, rgba(10,30,70,0) 50%);
  }
  .tile { position: absolute; width: 110px; height: 110px; }
  .tile--blue { background: var(--blue); }
  .tile--cyan { background: var(--cyan); }
  .tile--dark { background: var(--tile-dark); }
  .tile--slate { background: var(--slate); }
  .tile--mid { background: var(--blue-mid); }

  .back-brand {
    position: absolute; left: 330px; top: 150px; width: 350px;
    display: flex; align-items: center; gap: 16px;
  }
  .brand-mark { width: 22px; height: 22px; background: var(--white); flex: none; }
  .back-brand__name {
    font-family: "Jost", Futura, sans-serif; font-weight: 600;
    font-size: 34px; line-height: 1.2; letter-spacing: 1px;
    color: var(--white); text-transform: uppercase;
  }

  /* front face */
  .front-art { position: absolute; inset: 0; }
  .front-brand {
    position: absolute; left: 20px; top: 60px; width: 270px;
    display: flex; flex-direction: column; align-items: center; gap: 22px;
  }
  .brand-circle { width: 150px; height: 150px; border-radius: 50%; background: var(--navy); }
  .front-brand__name {
    font-family: "Jost", Futura, sans-serif; font-weight: 500;
    font-size: 22px; line-height: 1.25; text-align: center;
    color: var(--navy); text-transform: uppercase; letter-spacing: .5px;
  }

  .person { position: absolute; right: 30px; top: 36px; text-align: right; color: var(--white); }
  .person__name { font-size: 42px; line-height: 1.2; }
  .person__role { font-size: 24px; line-height: 1.2; }

  .contact-list { position: absolute; right: 22px; top: 226px; list-style: none; }
  .contact-list li {
    display: flex; justify-content: flex-end; align-items: center; gap: 12px;
    color: var(--white); font-size: 19px; line-height: 1.45;
  }
  .contact-icon { width: 20px; height: 20px; flex: none; }
</style>
</head>
<body>

<!-- Card back: equipment tiles and company name -->
<section class="card card--back" aria-label="Card back">
  <div class="backdrop-photo" role="img" aria-label="Faint photograph of gym weights in blue tones"></div>

  <div class="tile tile--dark"  style="left:300px; top:-20px;" role="img" aria-label="Locker icon tile"></div>
  <div class="tile tile--mid"   style="left:410px; top:-20px;" role="img" aria-label="Weight bench icon tile"></div>
  <div class="tile tile--blue"  style="left:0;     top:90px;"  role="img" aria-label="Shower icon tile"></div>
  <div class="tile tile--cyan"  style="left:110px; top:90px;"  role="img" aria-label="Exercise bike icon tile"></div>
  <div class="tile tile--slate" style="left:110px; top:200px;" role="img" aria-label="Kettlebell icon tile"></div>
  <div class="tile tile--blue"  style="left:220px; top:200px;" role="img" aria-label="Smoothie and apple icon tile"></div>
  <div class="tile tile--dark"  style="left:0;     top:310px;" role="img" aria-label="Skipping rope icon tile"></div>

  <div class="back-brand">
    <span class="brand-mark"></span>
    <span class="back-brand__name">Corvane Motion Limited</span>
  </div>
</section>

<!-- Card front: name and contact details -->
<section class="card card--front" aria-label="Card front">
  <svg class="front-art" width="700" height="400" viewBox="0 0 700 400" aria-hidden="true">
    <rect width="700" height="400" fill="var(--blue)"/>
    <polygon points="230,0 700,0 700,150 335,240" fill="var(--navy)"/>
    <polygon points="0,0 230,0 335,240 312,400 0,400" fill="var(--navy-deep)"/>
    <polygon points="0,0 218,0 320,238 298,400 0,400" fill="var(--paper)"/>
  </svg>

  <div class="front-brand">
    <span class="brand-circle"></span>
    <span class="front-brand__name">Corvane Motion Limited</span>
  </div>

  <div class="person">
    <p class="person__name">Owen Pritchard</p>
    <p class="person__role">Managing Director</p>
  </div>

  <ul class="contact-list">
    <li>+44 (0)7582 913 406
      <svg class="contact-icon" viewBox="0 0 20 20" aria-label="Phone"><rect width="20" height="20" fill="var(--white)"/><path d="M6 4h3l1 3-2 1.5a7 7 0 0 0 3.5 3.5L13 10l3 1v3c-5 1-11-5-10-10z" fill="var(--blue)"/></svg>
    </li>
    <li>sales@corvanemotion.co.uk
      <svg class="contact-icon" viewBox="0 0 20 20" aria-label="Email"><rect width="20" height="20" fill="var(--white)"/><rect x="4" y="6" width="12" height="8" fill="none" stroke="var(--blue)" stroke-width="1.5"/><path d="M4 6l6 5 6-5" fill="none" stroke="var(--blue)" stroke-width="1.5"/></svg>
    </li>
    <li>Corvanemotion.co.uk
      <svg class="contact-icon" viewBox="0 0 20 20" aria-label="Website"><rect width="20" height="20" fill="var(--white)"/><circle cx="10" cy="10" r="5.5" fill="none" stroke="var(--blue)" stroke-width="1.5"/><path d="M4.5 10h11M10 4.5v11" stroke="var(--blue)" stroke-width="1.2"/></svg>
    </li>
    <li>@motionLetterbin
      <span class="contact-icon" style="background:var(--white)"></span>
    </li>
    <li>Corvane Motion Limited
      <span class="contact-icon" style="background:var(--white)"></span>
    </li>
  </ul>
</section>

</body>
</html>
```